Crestline Staffing PEO - Web Build for Professional Employment Organization

We need a website built for our new PEO (professional employment organization). This company will offer third party Human Resource services to companies who are looking to outsource:<br/>Recruiting<br/>Administrative Onboarding<br/>New hire training, ongoing training and development<br/>Payroll/compensation processing/services<br/>Employee Relations<br/>Unemployment Claim Facilitation<br/>Benefits Plans and Administration<br/><br/>I have attached the logo below. Please use that as a reference and color match as best as possible. <br/><br/>Here are some of the competitor's websites:<br/>https://www.velmorahr.com/ <br/>https://www.trundelpay.com/<br/>https://www.trundelpay.com/<br/>https://www.qzn.com/<br/>https://www.bremwickhr.com/<br/>https://orvalepeo.com/contact-orvale/<br/><br/>

Target Market(s)

Startups and mid-sized businesses

Number of Pages Required

5+ page

Font styles to use
Sans Serif

Colors
0592cd

Requirements
Must have
• Features Pages
• SEO driven keyword rich content
• Strong focus on our ability to provide unemployment claim facilitation services as well as mandatory training/certification fulfillment
Nice to have
• I'd like to see one mockup with a Live Chat version if possible. In theory, the Live Chat messages would go directly to our front desk person.

```html
<!DOCTYPE html>
<html lang="en">
<head>
<meta charset="utf-8">
<title>Crestline Staffing PEO</title>
<link href="https://fonts.googleapis.com/css2?family=Arimo:wght@400;700&family=Roboto+Condensed:ital,wght@1,300;1,400&display=swap" rel="stylesheet">
<style>
:root{
  --brand:#0592cd;
  --navy:#2f3d6b;
  --ink:#111;
  --muted:#666;
  --soft:#f4f4f4;
  --header:#f1f1f1;
  --white:#fff;
}
*{box-sizing:border-box;margin:0;padding:0}
html,body{width:1200px;height:3256px;overflow:hidden}
body{position:relative;font-family:"Arimo",Arial,sans-serif;color:var(--ink);background:var(--white)}
.abs{position:absolute}

/* header */
.site-header{left:0;top:0;width:1200px;height:78px;background:var(--header)}
.brand{color:var(--navy);font-weight:700;font-size:23px;line-height:1;white-space:nowrap}
.nav a{position:absolute;top:35px;font-size:14px;color:var(--ink);text-decoration:none}

/* hero */
.hero{left:0;top:78px;width:1200px;height:543px;background:linear-gradient(100deg,#23386e 0%,#34497c 40%,#5b6478 70%,#3c4a6c 100%)}
.hero h1{left:111px;top:170px;color:var(--white);font-size:41px;line-height:45px;font-weight:700}
.hero p{left:111px;top:266px;width:540px;color:var(--white);font-size:14px;line-height:17px}
.btn-outline{left:111px;top:330px;width:121px;height:33px;border:1px solid var(--white);color:var(--white);font-size:13px;line-height:31px;text-align:center}

/* section headings */
.sec-title{left:0;width:1200px;font-size:27px;font-weight:700;text-align:center}
.sec-text{font-size:14px;line-height:17px;color:var(--muted);text-align:center}
.bar{height:5px;background:var(--brand)}

/* chat */
.chat{left:1040px;top:693px;width:160px;height:66px}
.chat-toggle{left:0;top:18px;width:34px;height:34px;border-radius:50%;background:var(--brand);border:2px solid #fff}
.chat-pill{left:34px;top:0;width:126px;height:66px;background:var(--brand);border-radius:33px 0 0 33px;color:#fff;font-size:14px}
.chat-pill span{position:absolute;left:57px;top:25px}

/* feature cards */
.feature{width:285px;height:337px;background:var(--white);box-shadow:0 1px 6px rgba(0,0,0,.22);border-bottom:4px solid var(--brand)}
.feature.alt{border-bottom-color:#222}
.feature .photo{position:absolute;left:17px;top:17px;width:253px;height:143px}
.feature h3{position:absolute;left:0;top:188px;width:100%;text-align:center;font-size:18px;font-weight:400}
.feature p{position:absolute;left:25px;top:226px;width:236px;font-size:11px;line-height:13px;color:var(--muted);text-align:justify}

/* services */
.what{left:0;top:1249px;width:1200px;height:1040px;background:var(--soft)}
.service{width:226px;height:316px;background:var(--white);border-radius:10px;box-shadow:0 1px 7px rgba(0,0,0,.25)}
.service .icon{position:absolute;left:80px;top:34px;width:64px;height:64px}
.service h3{position:absolute;left:23px;top:114px;width:180px;height:48px;display:flex;align-items:center;justify-content:center;text-align:center;font-size:14px;line-height:21px;font-weight:400}
.service p{position:absolute;left:20px;top:170px;width:186px;font-size:10px;line-height:17px;color:var(--muted);text-align:center}
.service .btn{position:absolute;left:38px;top:243px;width:150px;height:43px;border-radius:22px;background:var(--brand);color:#fff;font-size:16px;line-height:43px;text-align:center}

/* testimonial */
.why{left:0;top:2289px;width:1200px;height:555px;background:linear-gradient(120deg,#1b232e 0%,#2b3542 50%,#1d2631 100%)}
.why .sec-title{color:#fff;top:45px}
.avatar{left:165px;top:182px;width:202px;height:202px;border-radius:50%;background:linear-gradient(160deg,#b9c2cc,#6b4f3d 55%,#2f58a3)}
.person{left:166px;width:200px;color:#fff;text-align:center}
.quote-mark{color:#fff;font-family:"Roboto Condensed",sans-serif;font-style:italic;font-size:40px;font-weight:400}
.quote{left:425px;top:252px;width:560px;color:#fff;font-family:"Roboto Condensed",sans-serif;font-style:italic;font-weight:300;font-size:21px;line-height:26px;text-align:center}
.dot{width:10px;height:10px;border-radius:50%;background:#e5e5e5}
.dot.active{width:14px;height:14px;background:var(--brand)}

/* footer */
.footer-text{left:115px;top:3010px;width:285px;font-size:16px;line-height:26px;color:var(--muted);text-align:center}
.footer-head{font-size:17px;font-weight:700;color:#333}
.footer-links a{position:absolute;color:#555;text-decoration:none}
.info a{left:582px;font-size:13px}
.help a{left:865px;font-size:16px}
.rule{left:0;top:3216px;width:1200px;height:1px;background:var(--brand)}
.copyright{left:0;top:3230px;width:1200px;text-align:center;font-size:13px;color:#666}
</style>
</head>
<body>

<header class="site-header abs">
  <div class="brand abs" style="left:131px;top:28px">Crestline Staffing PEO</div>
  <nav class="nav">
    <a href="#" style="left:478px">HOME</a>
    <a href="#" style="left:563px">ABOUT US</a>
    <a href="#" style="left:679px">SERVICES</a>
    <a href="#" style="left:794px">PORTFOLIO</a>
    <a href="#" style="left:920px">BLOG</a>
    <a href="#" style="left:1003px">CONTACTUS</a>
  </nav>
</header>

<section class="hero abs" role="img" aria-label="Two colleagues working on a laptop in a modern office lounge">
  <h1 class="abs">STARTUP YOUR JOB<br>WITH US</h1>
  <p class="abs">Lorem Ipsum is simply dummy text of the printing and typesetting industry. Lorem Ipsum has been the industry's standard dummy text ever since the 1500s, when an unknown printer took a galley of type and scrambled it to make a type</p>
  <div class="btn-outline abs">Read More</div>
</section>

<h2 class="sec-title abs" style="top:684px;left:36px">WELCOME TO JOB STARTUP</h2>
<p class="sec-text abs" style="left:360px;top:730px;width:545px">Lorem Ipsum is simply dummy text of the printing and typesetting industry. Lorem Ipsum has been the industry's standard dummy text ever since the 1500s, when an unknown printer took a galley of type and scrambled it to make a type</p>
<div class="bar abs" style="left:516px;top:801px;width:219px"></div>

<aside class="chat abs">
  <div class="chat-pill abs">
    <svg class="abs" style="left:14px;top:14px" width="40" height="38" viewBox="0 0 40 38" fill="none" stroke="#fff" stroke-width="2"><path d="M14 6h20a4 4 0 0 1 4 4v9a4 4 0 0 1-4 4h-2v6l-6-6h-2"/><path d="M4 14h18a3 3 0 0 1 3 3v9a3 3 0 0 1-3 3H12l-6 5v-5H4a3 3 0 0 1-3-3v-9a3 3 0 0 1 3-3z"/><path d="M7 21h12M7 25h9"/></svg>
    <span>Chat us</span>
  </div>
  <div class="chat-toggle abs">
    <svg class="abs" style="left:10px;top:9px" width="12" height="14" viewBox="0 0 12 14"><path d="M10 1L2 7l8 6z" fill="#fff"/></svg>
  </div>
</aside>

<article class="feature abs" style="left:140px;top:854px">
  <div class="photo" role="img" aria-label="Three women smiling in a meeting" style="background:linear-gradient(120deg,#c9a98a,#4b3a33 60%,#7b8a9a)"></div>
  <h3>Job Consulting</h3>
  <p>Lorem Ipsum is simply dummy text of the printing and typesetting industry. Lorem Ipsum has been the industry's standard dummy text ever since the 1500s, when an</p>
</article>
<article class="feature abs" style="left:455px;top:854px">
  <div class="photo" role="img" aria-label="Team meeting around a white conference table" style="background:linear-gradient(180deg,#9aa1a8,#e8e8e8 55%,#cfcfcf)"></div>
  <h3>Marketing Analysis</h3>
  <p>Lorem Ipsum is simply dummy text of the printing and typesetting industry. Lorem Ipsum has been the industry's standard dummy text ever since the 1500s, when an</p>
</article>
<article class="feature alt abs" style="left:770px;top:854px">
  <div class="photo" role="img" aria-label="Businessmen reviewing documents at a desk" style="background:linear-gradient(180deg,#d6d9dc,#30343c 60%,#bfc3c8)"></div>
  <h3>Job Consulting</h3>
  <p>Lorem Ipsum is simply dummy text of the printing and typesetting industry. Lorem Ipsum has been the industry's standard dummy text ever since the 1500s, when an</p>
</article>

<section class="what abs"></section>
<h2 class="sec-title abs" style="top:1277px;left:6px">WHAT WE DO</h2>
<p class="sec-text abs" style="left:342px;top:1323px;width:545px">Lorem Ipsum is simply dummy text of the printing and typesetting industry. Lorem Ipsum has been the industry's standard dummy text ever since the 1500s, when an unknown printer took a galley of type and scrambled it to make a type</p>
<div class="bar abs" style="left:498px;top:1394px;width:219px"></div>

<svg width="0" height="0" style="position:absolute">
  <defs>
    <g id="search-person" fill="none" stroke="#0592cd" stroke-width="3" stroke-linecap="round">
      <circle cx="40" cy="24" r="19"/>
      <circle cx="40" cy="24" r="14"/>
      <circle cx="40" cy="19" r="4"/>
      <path d="M32 31c2-5 14-5 16 0"/>
      <path d="M26 38L8 56a4 4 0 0 0 6 6l18-18"/>
    </g>
  </defs>
</svg>

<div class="service abs" style="left:114px;top:1431px">
  <svg class="icon" viewBox="0 0 64 64"><use href="#search-person"/></svg>
  <h3>Recruiting</h3>
  <p>Lorem Ipsum is simply dummy text of the printing and typesetting industry. Lorem Ipsum has been the industry's</p>
  <div class="btn">Read More</div>
</div>
<div class="service abs" style="left:364px;top:1431px">
  <svg class="icon" viewBox="0 0 64 64"><use href="#search-person"/></svg>
  <h3>Administrative<br>Onboarding</h3>
  <p>Lorem Ipsum is simply dummy text of the printing and typesetting industry. Lorem Ipsum has been the industry's</p>
  <div class="btn">Read More</div>
</div>
<div class="service abs" style="left:613px;top:1431px">
  <svg class="icon" viewBox="0 0 64 64"><use href="#search-person"/></svg>
  <h3>New hire training, ongoing training and development</h3>
  <p>Lorem Ipsum is simply dummy text of the printing and typesetting industry. Lorem Ipsum has been the industry's</p>
  <div class="btn">Read More</div>
</div>
<div class="service abs" style="left:861px;top:1431px">
  <svg class="icon" viewBox="0 0 64 64"><use href="#search-person"/></svg>
  <h3>Payroll/compensation processing/services</h3>
  <p>Lorem Ipsum is simply dummy text of the printing and typesetting industry. Lorem Ipsum has been the industry's</p>
  <div class="btn">Read More</div>
</div>

<div class="service abs" style="left:204px;top:1863px">
  <svg class="icon" viewBox="0 0 64 64"><use href="#search-person"/></svg>
  <h3>Employee Relations</h3>
  <p>Lorem Ipsum is simply dummy text of the printing and typesetting industry. Lorem Ipsum has been the industry's</p>
  <div class="btn">Read More</div>
</div>
<div class="service abs" style="left:492px;top:1863px">
  <svg class="icon" viewBox="0 0 64 64"><use href="#search-person"/></svg>
  <h3>Unemployment Claim<br>Facilitation</h3>
  <p>Lorem Ipsum is simply dummy text of the printing and typesetting industry. Lorem Ipsum has been the industry's</p>
  <div class="btn">Read More</div>
</div>
<div class="service abs" style="left:783px;top:1863px">
  <svg class="icon" viewBox="0 0 64 64"><use href="#search-person"/></svg>
  <h3>Benefits Plans and<br>Administration</h3>
  <p>Lorem Ipsum is simply dummy text of the printing and typesetting industry. Lorem Ipsum has been the industry's</p>
  <div class="btn">Read More</div>
</div>

<section class="why abs" role="img" aria-label="Dark background of a person writing notes on paper at a desk">
  <h2 class="sec-title abs">WHY CHOOSE CRESTLINE STAFFING?</h2>
  <div class="bar abs" style="left:498px;top:83px;width:219px"></div>
  <div class="avatar abs" role="img" aria-label="Portrait of a smiling man in a blue blazer"></div>
  <div class="person abs" style="top:413px;font-size:18px;font-weight:700">Marcus Delane</div>
  <div class="person abs" style="top:441px;font-size:12px">Designer, Halvick</div>
  <div class="quote-mark abs" style="left:417px;top:175px">//</div>
  <p class="quote abs">Lorem ipsum dolor sit amet, consectetur adipiscing elit, sed do eiusmod tempor incididunt ut labore et dolore magna aliqua. Quis ipsum suspendisse ultrices gravida. Risus commodo viverra maecenas accumsan lacus vel facilisis.</p>
  <div class="quote-mark abs" style="left:987px;top:335px">//</div>
  <div class="dot abs" style="left:594px;top:493px"></div>
  <div class="dot active abs" style="left:614px;top:491px"></div>
  <div class="dot abs" style="left:637px;top:493px"></div>
  <div class="dot abs" style="left:659px;top:493px"></div>
</section>

<footer>
  <div class="brand abs" style="left:131px;top:2940px">Crestline Staffing PEO</div>
  <p class="footer-text abs">Lorem Ipsum is simply dummy text of the printing and typesetting industry. Lorem Ipsum has been the industry's standard dummy text ever since the 1500s, when an unknown printer took a galley of type and scrambled it to make a type</p>

  <div class="footer-head abs" style="left:582px;top:2926px">INFORMATION</div>
  <nav class="footer-links info">
    <a href="#" style="top:2977px">HOME</a>
    <a href="#" style="top:3015px">ABOUT US</a>
    <a href="#" style="top:3053px">SERVICES</a>
    <a href="#" style="top:3091px">PORTFOLIO</a>
    <a href="#" style="top:3129px">BLOG</a>
    <a href="#" style="top:3167px">CONTACTUS</a>
  </nav>

  <div class="footer-head abs" style="left:865px;top:2926px">HELP &amp; SUPPORT</div>
  <nav class="footer-links help">
    <a href="#" style="top:2974px">Contacts</a>
    <a href="#" style="top:3012px">My Account</a>
    <a href="#" style="top:3050px">Cart</a>
  </nav>

  <div class="rule abs"></div>
  <p class="copyright abs">Copyright © 2006-2020 Crestline Staffing</p>
</footer>

</body>
</html>
```